Business Card Design using new attached logo

We are a family run Plumbing and Heating firm looking to improve our company image with an improved business card and new logo.We are looking to keep the company colour (Blue) involved in our design

Reason: New logo added which needs to be incorporated on designs

Industry/Entity Type

Business

Contact Information for Business Card

See attachment of all info required.

Requirements
Must have
• We have just picked a new company logo which is attached.
• Could you please provide your business card designs using this logo.
• We are looking for the logo on the back as well as the front with all the info required

```html
<!DOCTYPE html>
<html lang="en">
<head>
<meta charset="utf-8">
<title>Northway Services – Business Card</title>
<link rel="stylesheet" href="https://fonts.googleapis.com/css2?family=Cinzel:wght@600&family=Open+Sans:ital,wght@0,400;0,600;1,400&display=swap">
<style>
  :root {
    --stage: #333333;
    --navy-edge: #1f3a78;
    --blue-glow: #3a88cc;
    --card-white: #ffffff;
    --ink-white: #ffffff;
    --brand-blue: #25437f;
    --tagline-blue: #2b3f7c;
  }
  * { margin: 0; padding: 0; box-sizing: border-box; }
  html, body {
    width: 1200px; height: 907px; overflow: hidden;
    background: var(--stage);
  }
  .card {
    position: absolute; left: 300px; width: 601px; height: 343px;
    box-shadow: 0 3px 8px rgba(0,0,0,0.55);
  }
  .card-front {
    top: 92px;
    background: radial-gradient(ellipse 62% 68% at 49% 48%, var(--blue-glow) 0%, #2c66ab 45%, var(--navy-edge) 100%);
    color: var(--ink-white);
  }
  .card-back { top: 472px; background: var(--card-white); }

  .holder-name {
    position: absolute; left: 41px; top: 27px;
    font: 600 22px/1 "Cinzel", serif; letter-spacing: 0.5px;
  }
  .holder-role {
    position: absolute; left: 41px; top: 57px;
    font: 600 17px/1 "Cinzel", serif; letter-spacing: 0.5px;
  }
  .header-rule {
    position: absolute; left: 41px; top: 95px; width: 515px; height: 1px;
    background: var(--ink-white); opacity: 0.85;
  }
  .brand-front {
    position: absolute; right: 45px; top: 40px;
    font: 600 34px/1 "Open Sans", sans-serif; letter-spacing: 0.5px;
    color: var(--ink-white);
  }
  .address {
    position: absolute; left: 41px; top: 112px;
    font: 400 15.5px/22px "Open Sans", sans-serif;
  }
  .contacts { position: absolute; left: 41px; top: 189px; list-style: none; }
  .contacts li {
    display: flex; align-items: center; height: 24px;
    font: 400 15.5px/1 "Open Sans", sans-serif;
  }
  .contacts svg { width: 16px; height: 16px; margin: 0 10px 0 1px; fill: var(--ink-white); }

  .brand-back {
    position: absolute; left: 0; right: 0; top: 140px;
    display: flex; justify-content: center; align-items: center; gap: 14px;
    font: 600 48px/1 "Open Sans", sans-serif; color: var(--brand-blue);
  }
  .brand-dot { width: 22px; height: 22px; border-radius: 50%; background: var(--brand-blue); }
  .tagline {
    position: absolute; left: 0; right: 0; top: 283px; text-align: center;
    font: italic 400 16px/1 "Open Sans", sans-serif; color: var(--tagline-blue);
    letter-spacing: 0.3px;
  }
</style>
</head>
<body>
  <section class="card card-front">
    <h1 class="holder-name">Daniel Hartley</h1>
    <p class="holder-role">Director</p>
    <div class="brand-front">Northway</div>
    <div class="header-rule"></div>
    <address class="address" style="font-style:normal">
      Northway Services Ltd<br>
      14 Mill Parade, Elmfield Road<br>
      Kingsford, KF27LP
    </address>
    <ul class="contacts">
      <li><svg viewBox="0 0 16 16" aria-hidden="true"><path d="M4 1c1 0 2 3 2 4s-1.5 1.2-1.2 2.2c.6 1.6 2.2 3.4 3.8 4 1 .3 1.3-1.2 2.3-1.2s4 1 4 2-1.6 3-3.4 3C6.5 15 1 9.5 1 4.4 1 2.6 3 1 4 1z"/></svg>020 7946 0321</li>
      <li><svg viewBox="0 0 16 16" aria-hidden="true"><path d="M4 1h8v4H4zM1 6h14v6h-2v3H3v-3H1zm4 4v3.5h6V10z"/></svg>020 7946 0587</li>
      <li><svg viewBox="0 0 16 16" aria-hidden="true"><path d="M5 0h1v2h5a1 1 0 0 1 1 1v12a1 1 0 0 1-1 1H5a1 1 0 0 1-1-1V3a1 1 0 0 1 1-1zm1 4v4h4V4zm0 6v1h1v-1zm2 0v1h1v-1zm-2 2v1h1v-1zm2 0v1h1v-1z"/></svg>07700900418</li>
      <li><svg viewBox="0 0 16 16" aria-hidden="true"><path d="M1 4h14v1L8 9.5 1 5zm0 2.5 7 4.5 7-4.5V12H1z"/></svg>danielhartley@northwayservices.co.uk</li>
      <li><svg viewBox="0 0 16 16" aria-hidden="true"><path fill="none" stroke="#fff" stroke-width="1.1" d="M8 1.5a6.5 6.5 0 1 0 .01 0zM1.5 8h13M8 1.5c-3 3.5-3 9.5 0 13M8 1.5c3 3.5 3 9.5 0 13M2.5 4.8h11M2.5 11.2h11"/></svg>www.northwayservices.co.uk</li>
    </ul>
  </section>

  <section class="card card-back">
    <div class="brand-back"><span class="brand-dot"></span>Northway</div>
    <p class="tagline">Plumbing and Heating Services</p>
  </section>
</body>
</html>
```